Business Card Design

Hi I need a business card designed, we already have the business name logo artwork and would like some concept ideas for the Bus Card layout.
On the back of the card i want to include the products and services that we offer.
We are a Plastics Sheeting manufacture based in Perth Australia.

                                       

We need a BC design for a company called Tarvo Plastics based in Perth Australia.

We supply from DIY to Trade & Industrial  Engineering Markets.

We specialise in:

·         Cut to size panels  (all shapes and sizes)

·         Plastics fabrication & Welding

·         Custom Designs

·         Plastic Repairs

·         PVC Pipe Slotting & PVC Pipe Threading

·         Supplier of all types of engineering plastics and profiles.

Including:           Acrylic / Clarvene

                               Polycarbonate / Dorvil

                               Prismatic Light Diffuser

                               Vantrib

                               HDPE / UHMWPE

                               PVC / PVC Foam

                               Nylon

                               HIPS

```html
<!DOCTYPE html>
<html lang="en">
<head>
<meta charset="utf-8">
<title>Tarvo Plastics – Business Card</title>
<link href="https://fonts.googleapis.com/css2?family=Open+Sans:wght@400;600;700;800&display=swap" rel="stylesheet">
<style>
  :root {
    --navy: #1f2f63;
    --orange: #ec7a1c;
    --ink: #4a4a4a;
    --paper: #ffffff;
    --stage: #e9e6e1;
    --rule: #c9c9c9;
  }
  * { box-sizing: border-box; margin: 0; padding: 0; }
  html, body { width: 1200px; height: 720px; overflow: hidden; }
  body {
    background: var(--stage);
    font-family: "Open Sans", Arial, sans-serif;
    color: var(--ink);
    display: flex;
    align-items: center;
    justify-content: center;
    gap: 40px;
  }
  .card {
    position: relative;
    width: 540px;
    height: 330px;
    background: var(--paper);
    overflow: hidden;
    box-shadow: 0 2px 8px rgba(0,0,0,.18);
  }
  .brand {
    display: flex;
    align-items: center;
    gap: 10px;
    color: var(--navy);
    font-weight: 800;
    font-size: 42px;
    line-height: 1;
    letter-spacing: -0.5px;
    white-space: nowrap;
  }
  .brand-mark { width: 22px; height: 22px; background: var(--orange); flex: none; }

  /* Front */
  .front .brand { position: absolute; top: 40px; left: 60px; }
  .holder { position: absolute; top: 130px; left: 40px; font-size: 17px; font-weight: 700; color: var(--navy); }
  .holder .title { color: var(--orange); font-weight: 400; }
  .contacts { position: absolute; top: 166px; left: 40px; list-style: none; font-size: 13px; line-height: 21px; }
  .contacts li { display: flex; align-items: center; gap: 7px; }
  .contacts svg { width: 12px; height: 12px; fill: var(--ink); }
  .address { position: absolute; left: 40px; bottom: 44px; font-size: 13px; white-space: nowrap; }
  .band { position: absolute; left: 0; bottom: 0; width: 540px; height: 30px; }
  .band-text { position: absolute; bottom: 0; height: 30px; line-height: 30px; color: #fff; white-space: nowrap; }
  .band-po { left: 30px; font-size: 12px; }
  .band-legal { right: 12px; font-weight: 600; font-size: 11px; }

  /* Back */
  .back .brand { position: absolute; top: 24px; left: 50%; transform: translateX(-50%); font-size: 40px; }
  .headline {
    position: absolute; top: 82px; left: 0; width: 100%;
    text-align: center; color: var(--navy); font-weight: 700; font-size: 14px; line-height: 18px;
  }
  .col { position: absolute; top: 138px; }
  .col-services { left: 26px; width: 280px; }
  .col-materials { left: 330px; width: 200px; }
  .col-heading { color: var(--navy); font-weight: 700; font-size: 16px; margin-bottom: 4px; }
  .list { list-style: none; font-size: 12.5px; line-height: 18px; }
  .list li { position: relative; padding-left: 12px; }
  .list li::before {
    content: ""; position: absolute; left: 0; top: 7px;
    width: 5px; height: 5px; border-radius: 50%; background: var(--orange);
  }
  .list .pair { display: flex; gap: 14px; padding-left: 0; }
  .list .pair::before { display: none; }
  .list .pair span { position: relative; padding-left: 12px; }
  .list .pair span::before {
    content: ""; position: absolute; left: 0; top: 7px;
    width: 5px; height: 5px; border-radius: 50%; background: var(--orange);
  }
  .divider { position: absolute; left: 312px; top: 132px; width: 1px; height: 150px; background: var(--rule); }
</style>
</head>
<body>

  <section class="card front" aria-label="Card front">
    <div class="brand"><span class="brand-mark"></span>Tarvo Plastics</div>

    <p class="holder">Your Name, <span class="title">Title</span></p>

    <ul class="contacts">
      <li><svg viewBox="0 0 12 12"><path d="M3 1l2 2-1 1.5c.7 1.4 1.8 2.5 3.2 3.2L8.7 6.7l2 2-1.5 2C5 10.3 1.7 7 1.3 2.5z"/></svg>08 9400 3170</li>
      <li><svg viewBox="0 0 12 12"><rect x="3" y="0.5" width="6" height="11" rx="1"/><rect x="4" y="2" width="4" height="6" fill="#fff"/></svg>0412 555 019</li>
      <li><svg viewBox="0 0 12 12"><rect x="1" y="4" width="10" height="6" rx="1"/><rect x="3" y="1" width="6" height="3"/><rect x="3" y="7" width="6" height="4" fill="#fff"/></svg>08 9400 3171</li>
      <li><svg viewBox="0 0 12 12"><rect x="0.5" y="2" width="11" height="8" rx="1"/><path d="M1 2.5l5 4 5-4" stroke="#fff" fill="none"/></svg>sales@tarvoplastics.com.au</li>
    </ul>

    <p class="address">Unit 4/18 Kestrel Way Southgate WA 6150</p>

    <svg class="band" viewBox="0 0 540 30" preserveAspectRatio="none" aria-hidden="true">
      <polygon points="0,0 252,0 242,30 0,30" fill="var(--orange)"/>
      <polygon points="252,0 540,0 540,30 242,30" fill="var(--navy)"/>
    </svg>
    <p class="band-text band-po">PO Box 2280 Southgate DC WA 6971</p>
    <p class="band-text band-legal">Orren Holdings Pty Ltd T/A Tarvo Plastics ABN:TBA</p>
  </section>

  <section class="card back" aria-label="Card back">
    <div class="brand"><span class="brand-mark"></span>Tarvo Plastics</div>

    <p class="headline">The Products And Services That We Offer<br>Are Supplied From Diy To Trade &amp; Industrial Engineering Markets</p>

    <div class="col col-services">
      <h2 class="col-heading">We specialise in:</h2>
      <ul class="list">
        <li>Cut to size panels (all shapes and sizes)</li>
        <li>Plastics fabrication &amp; Welding</li>
        <li>Custom Designs</li>
        <li>Plastic Repairs</li>
        <li>PVC Pipe Slotting &amp; PVC Pipe Threading</li>
        <li>Supplier of all types of engineering plastics and profiles</li>
      </ul>
    </div>

    <div class="divider"></div>

    <div class="col col-materials">
      <h2 class="col-heading">Including:</h2>
      <ul class="list">
        <li>Acrylic / Clarvene</li>
        <li>Polycarbonate / Dorvil</li>
        <li>Prismatic Light Diffuser</li>
        <li class="pair"><span>Vantrib</span><span>HDPE / UHMWPE</span></li>
        <li>PVC / PVC Foam</li>
        <li class="pair"><span>Nylon</span><span>HIPS</span></li>
      </ul>
    </div>
  </section>

</body>
</html>
```